Goodlooking website for a company who is working in the IT consultancy

We want a new website designed in WordPress. You can take www.vantoro.nl as an example. It should be a website with some short blocks of information about the company, nice pictures of our partners and our employees. A job page with a clear filter.

Target Market(s)

B2B

Industry/Entity Type

It Company

Coding

Coded - Design and coding required

Number of Pages Required

5+ page

Font styles to use
Sans Serif

Colors
0455a3
34a7d8

Requirements
Must have
• Check briefing

```html
<!DOCTYPE html>
<html lang="en">
<head>
<meta charset="utf-8">
<title>Nexora – Critical IT Systems</title>
<link href="https://fonts.googleapis.com/css2?family=Raleway:wght@500;600;700&family=Open+Sans:wght@400;600&display=swap" rel="stylesheet">
<style>
:root{
  --teal:#1fa6a6;
  --teal-dark:#137f86;
  --ink:#10181f;
  --navy:#0f2a36;
  --text:#444c52;
  --muted:#7b8790;
  --light:#f3f5f6;
  --white:#ffffff;
  --line:#dde3e6;
}
*{box-sizing:border-box;margin:0;padding:0}
html,body{width:1200px;height:4380px;overflow:hidden}
body{position:relative;font-family:"Open Sans",Arial,sans-serif;color:var(--text);background:var(--white)}
.abs{position:absolute}
h2{font-family:"Raleway",Arial,sans-serif;font-weight:600;color:var(--ink);font-size:27px;letter-spacing:.5px}
.lead{font-size:12px;line-height:21px;color:var(--text)}
.center{text-align:center}
.btn{display:inline-block;background:var(--teal);color:var(--white);font-family:"Raleway",Arial,sans-serif;font-weight:700;font-size:12px;border-radius:20px;letter-spacing:.5px}
.brand{display:flex;align-items:center;gap:12px;font-family:"Raleway",Arial,sans-serif;font-weight:700;letter-spacing:3px}
.brand-dot{border-radius:50%;background:var(--teal)}

/* header */
.topline{left:0;top:0;width:1200px;height:5px;background:linear-gradient(90deg,var(--teal),#0455a3)}
.site-header{left:0;top:5px;width:1200px;height:100px;background:var(--white)}
.site-header .brand{position:absolute;left:160px;top:22px;color:var(--navy);font-size:30px}
.site-header .brand-dot{width:56px;height:56px}
.search{position:absolute;left:840px;top:20px;width:200px;height:34px;border:1px solid var(--line);border-radius:17px;font-size:11px;color:var(--text);padding:9px 14px}
.search svg{position:absolute;right:12px;top:10px}
.nav{position:absolute;top:72px;left:622px;display:flex;gap:0;font-family:"Raleway",Arial,sans-serif;font-weight:700;font-size:13px;color:var(--navy)}
.nav span{position:absolute;white-space:nowrap}
.nav .active{color:var(--teal)}

/* hero */
.hero{left:0;top:105px;width:1200px;height:620px;background:linear-gradient(160deg,#2b7f8c 0%,#1c6472 45%,#0f3c4a 100%);clip-path:polygon(0 0,100% 0,100% 92%,0 100%)}
.hero-photo{position:absolute;inset:0;background:linear-gradient(120deg,rgba(255,255,255,.08),rgba(0,0,0,.15))}
.hero .brand{position:absolute;left:405px;top:145px;color:var(--white);font-size:60px}
.hero .brand-dot{width:100px;height:100px;background:transparent;border:5px solid var(--white)}
.hero-title{position:absolute;left:0;width:1200px;top:265px;text-align:center;font-family:"Raleway",Arial,sans-serif;font-weight:600;font-size:33px;line-height:46px;color:var(--white)}
.dots{position:absolute;top:468px;left:514px;display:flex;gap:6px}
.dots i{display:block;width:40px;height:4px;background:rgba(255,255,255,.9)}
.dots i.on{background:rgba(255,255,255,.45)}

/* services */
.services{left:0;top:640px;width:1200px;height:700px;background:linear-gradient(180deg,#15262e,#0d161c);z-index:-1}
.services-title{left:0;top:745px;width:1200px;color:var(--white)}
.services-lead{left:280px;top:795px;width:640px;color:#c6ced3;font-size:11px}
.card{top:870px;width:278px;height:300px;background:var(--white);text-align:center;padding-top:30px}
.card .ico{width:112px;height:112px;border:3px solid var(--navy);border-radius:50%;margin:0 auto}
.card h3{font-family:"Raleway",Arial,sans-serif;font-weight:700;font-size:15px;color:var(--ink);margin:26px 0 14px}
.card p{font-size:11px;line-height:19px;padding:0 30px}

/* about */
.about{left:0;top:1255px;width:1200px;height:665px;background:linear-gradient(90deg,#e4f4f6 0%,#d6eef1 45%,#bcdde3 100%);clip-path:polygon(0 6%,100% 0,100% 95%,0 100%)}
.about-photo{position:absolute;right:0;top:0;width:560px;height:100%;background:linear-gradient(90deg,rgba(214,238,241,0) 0%,#a9cdd6 40%,#8fb8c4 100%)}
.block-text{width:480px}
.block-text h2{font-size:26px;margin-bottom:16px}
.block-text p{font-size:11px;line-height:20px}
.block-text .btn{margin-top:22px;padding:9px 20px}

/* jobs */
.jobs-title{left:0;top:1940px;width:1200px}
.jobs-lead{left:280px;top:1990px;width:640px;font-size:11px}
.job-list{left:160px;top:2065px;width:880px}
.job{position:relative;height:66px;margin-bottom:8px;background:var(--light);box-shadow:0 1px 3px rgba(0,0,0,.12);display:flex;align-items:center}
.job-title{position:absolute;left:38px;font-size:16px;color:var(--ink)}
.job-loc{position:absolute;left:485px;font-size:12px;color:var(--muted);display:flex;align-items:center;gap:8px}
.tag{position:absolute;right:24px;width:92px;height:30px;line-height:30px;border-radius:15px;text-align:center;font-family:"Raleway",Arial,sans-serif;font-weight:700;font-size:11px;color:var(--white);background:var(--teal)}
.tag.part{background:var(--navy)}
.view-all{left:0;width:1200px;top:2477px;text-align:center;font-family:"Raleway",Arial,sans-serif;font-weight:700;font-size:14px;color:var(--ink)}
.view-all span{border-bottom:2px solid var(--ink);padding-bottom:3px}

/* what we do */
.what{left:0;top:2545px;width:1200px;height:670px;background:linear-gradient(90deg,#cfe6ea 0%,#e6f3f5 50%,#f2f8f9 100%);clip-path:polygon(0 7%,100% 0,100% 94%,0 100%)}
.what-photo{position:absolute;left:0;top:0;width:560px;height:100%;background:linear-gradient(90deg,#7aa3ad 0%,#a9c8cf 55%,rgba(230,243,245,0) 100%)}

/* contact */
.contact-band{left:0;top:3220px;width:1200px;height:520px;background:linear-gradient(180deg,#ffffff 0%,#ffffff 35%,#dff2f4 75%,#ffffff 100%);z-index:-1}
.contact-title{left:0;top:3265px;width:1200px}
.contact-lead{left:355px;top:3315px;width:490px;font-size:11px}
.field{left:328px;width:252px;height:30px;border:1px solid #b7c2c8;background:var(--white);font-size:10px;padding:7px 8px;color:var(--text)}
.message{left:586px;top:3382px;width:286px;height:132px;border:1px solid #b7c2c8;background:var(--white);font-size:10px;padding:6px 8px}
.contact-btn{left:488px;top:3530px;width:224px;height:44px;line-height:44px;text-align:center;border-radius:22px;font-size:14px}

/* partners */
.partners-title{left:0;top:3740px;width:1200px}
.partners-lead{left:355px;top:3785px;width:490px;font-size:11px}
.badge{top:3855px;height:60px;background:#c9ced2;border-radius:4px}

/* footer */
.footer{left:0;top:4060px;width:1200px;height:320px;background:linear-gradient(180deg,#141e25,#0c1217)}
.footer .brand{position:absolute;left:160px;top:110px;color:var(--white);font-size:40px}
.footer .brand-dot{width:60px;height:60px}
.fcol{position:absolute;top:48px;color:#c6ced3;font-size:12px;line-height:23px}
.fcol h4{font-family:"Raleway",Arial,sans-serif;font-weight:600;font-size:17px;color:var(--white);margin-bottom:14px}
.fcol .row{display:flex;align-items:center;gap:8px}
.copy{position:absolute;left:160px;top:270px;font-size:11px;color:#c6ced3}
.social{position:absolute;left:905px;top:258px;display:flex;gap:10px}
.social i{display:block;width:26px;height:26px;border-radius:50%;background:var(--teal)}
</style>
</head>
<body>

<div class="abs topline"></div>
<header class="abs site-header">
  <div class="brand"><span class="brand-dot"></span>NEXORA</div>
  <div class="search">Zoek
    <svg width="12" height="12" viewBox="0 0 12 12"><circle cx="5" cy="5" r="3.8" fill="none" stroke="#10181f" stroke-width="1.5"/><line x1="8" y1="8" x2="11" y2="11" stroke="#10181f" stroke-width="1.5"/></svg>
  </div>
  <nav class="nav">
    <span class="active" style="left:0">HOME</span>
    <span style="left:73px">OUR SOLUTIONS</span>
    <span style="left:204px">OUR TEAM</span>
    <span style="left:301px">JOB</span>
    <span style="left:359px">CONTACT</span>
  </nav>
</header>

<section class="abs hero">
  <div class="hero-photo" role="img" aria-label="Team of colleagues meeting in a bright office, teal tinted"></div>
  <div class="brand"><span class="brand-dot"></span>NEXORA</div>
  <div class="hero-title">WE SHARE OUR KNOWLEDGE<br>WITH CUSTOMERS</div>
  <div class="dots"><i></i><i></i><i class="on"></i><i></i></div>
</section>

<div class="abs services"></div>
<h2 class="abs services-title center">NEXORA IT SERVICES</h2>
<p class="abs services-lead lead center">Sed ut perspiciatis unde omnis iste natus error sit voluptatem accusantium doloremque laudantium, totam rem aperiam, eaque ipsa quae ab illo inventore veritatis et quasi architecto beatae vitae dicta sunt explicabo. Nemo enim ipsam voluptatem.</p>

<div class="abs card" style="left:163px">
  <div class="ico"><svg width="106" height="106" viewBox="0 0 106 106"><rect x="34" y="32" width="42" height="30" fill="none" stroke="#0f2a36" stroke-width="3"/><circle cx="30" cy="50" r="5" fill="#1fa6a6"/><line x1="30" y1="56" x2="30" y2="76" stroke="#0f2a36" stroke-width="4"/><line x1="40" y1="62" x2="40" y2="76" stroke="#0f2a36" stroke-width="3"/></svg></div>
  <h3>TRAINING</h3>
  <p>Sed ut perspiciatis unde omnis iste na sit voluptatem accusantium doloremquem, totam rem aperiam, eaque ipsa quae abo</p>
</div>
<div class="abs card" style="left:461px">
  <div class="ico"><svg width="106" height="106" viewBox="0 0 106 106"><circle cx="40" cy="38" r="7" fill="#0f2a36"/><circle cx="66" cy="58" r="7" fill="#1fa6a6"/><rect x="28" y="48" width="24" height="12" rx="4" fill="#0f2a36"/><rect x="54" y="68" width="24" height="12" rx="4" fill="#1fa6a6"/></svg></div>
  <h3>PERSONAL COACHING</h3>
  <p>Sed ut perspiciatis unde omnis iste na sit voluptatem accusantium doloremquem, totam rem aperiam, eaque ipsa quae abo</p>
</div>
<div class="abs card" style="left:762px">
  <div class="ico"><svg width="106" height="106" viewBox="0 0 106 106"><rect x="30" y="28" width="46" height="34" fill="none" stroke="#0f2a36" stroke-width="3"/><rect x="40" y="46" width="6" height="12" fill="#1fa6a6"/><rect x="50" y="40" width="6" height="18" fill="#1fa6a6"/><rect x="60" y="34" width="6" height="24" fill="#1fa6a6"/><line x1="53" y1="62" x2="53" y2="78" stroke="#0f2a36" stroke-width="3"/></svg></div>
  <h3>EDUCATION TRAJECTS</h3>
  <p>Sed ut perspiciatis unde omnis iste na sit voluptatem accusantium doloremquem, totam rem aperiam, eaque ipsa quae abo</p>
</div>

<section class="abs about">
  <div class="about-photo" role="img" aria-label="Smiling woman working on a laptop with a coffee cup"></div>
  <div class="abs block-text" style="left:162px;top:225px">
    <h2>ABOUT US</h2>
    <p>Sed ut perspiciatis unde omnis iste natus error sit voluptatem accusantium doloremque laudantium, totam rem aperiam, eaque ipsa quae ab illo inventore veritatis et quasi architecto beatae vitae dicta sunt explicabo. Nemo enim ipsam voluptatem quia voluptas sit aspernatur aut odit aut fugit, sed quia consequuntur magni dolores eos qui ratione voluptatem sequi nesciunt. Neque porro quisquam est, qui dolorem ipsum quia dolor sit amet, consectetur, adipisci velit, sed quia non numquam eius modi tempora incidunt ut labore et dolore magnam aliquam quaerat voluptatem.</p>
    <span class="btn">READ MORE</span>
  </div>
</section>

<h2 class="abs jobs-title center">JOB LISTING</h2>
<p class="abs jobs-lead lead center">Sed ut perspiciatis unde omnis iste natus error sit voluptatem accusantium doloremque laudantium, totam rem aperiam, eaque ipsa quae ab illo inventore veritatis et quasi architecto beatae vitae dicta sunt explicabo. Nemo enim ipsam voluptatem.</p>

<div class="abs job-list">
  <div class="job"><span class="job-title">Sed ut perspiciatis unde omnis iste natus</span><span class="job-loc"><svg width="10" height="14" viewBox="0 0 10 14"><path d="M5 0a5 5 0 0 1 5 5c0 4-5 9-5 9S0 9 0 5a5 5 0 0 1 5-5z" fill="#1fa6a6"/><circle cx="5" cy="5" r="2" fill="#fff"/></svg>Location Name, City Name</span><span class="tag">FULL TIME</span></div>
  <div class="job"><span class="job-title">Sed ut perspiciatis unde omnis iste natus</span><span class="job-loc"><svg width="10" height="14" viewBox="0 0 10 14"><path d="M5 0a5 5 0 0 1 5 5c0 4-5 9-5 9S0 9 0 5a5 5 0 0 1 5-5z" fill="#1fa6a6"/><circle cx="5" cy="5" r="2" fill="#fff"/></svg>Location Name, City Name</span><span class="tag">FULL TIME</span></div>
  <div class="job"><span class="job-title">Sed ut perspiciatis unde omnis iste natus</span><span class="job-loc"><svg width="10" height="14" viewBox="0 0 10 14"><path d="M5 0a5 5 0 0 1 5 5c0 4-5 9-5 9S0 9 0 5a5 5 0 0 1 5-5z" fill="#1fa6a6"/><circle cx="5" cy="5" r="2" fill="#fff"/></svg>Location Name, City Name</span><span class="tag part">PART TIME</span></div>
  <div class="job"><span class="job-title">Sed ut perspiciatis unde omnis iste natus</span><span class="job-loc"><svg width="10" height="14" viewBox="0 0 10 14"><path d="M5 0a5 5 0 0 1 5 5c0 4-5 9-5 9S0 9 0 5a5 5 0 0 1 5-5z" fill="#1fa6a6"/><circle cx="5" cy="5" r="2" fill="#fff"/></svg>Location Name, City Name</span><span class="tag">FULL TIME</span></div>
  <div class="job"><span class="job-title">Sed ut perspiciatis unde omnis iste natus</span><span class="job-loc"><svg width="10" height="14" viewBox="0 0 10 14"><path d="M5 0a5 5 0 0 1 5 5c0 4-5 9-5 9S0 9 0 5a5 5 0 0 1 5-5z" fill="#1fa6a6"/><circle cx="5" cy="5" r="2" fill="#fff"/></svg>Location Name, City Name</span><span class="tag part">PART TIME</span></div>
</div>
<div class="abs view-all"><span>VIEW ALL JOBS</span></div>

<section class="abs what">
  <div class="what-photo" role="img" aria-label="Smiling businesswoman holding a tablet"></div>
  <div class="abs block-text" style="left:566px;top:205px">
    <h2>WHAT WE DO</h2>
    <p>Sed ut perspiciatis unde omnis iste natus error sit voluptatem accusantium doloremque laudantium, totam rem aperiam, eaque ipsa quae ab illo inventore veritatis et quasi architecto beatae vitae dicta sunt explicabo. Nemo enim ipsam voluptatem quia voluptas sit aspernatur aut odit aut fugit, sed quia consequuntur magni dolores eos qui ratione voluptatem sequi nesciunt. Neque porro quisquam est, qui dolorem ipsum quia dolor sit amet, consectetur, adipisci velit, sed quia non numquam eius modi tempora incidunt ut labore et dolore magnam aliquam quaerat voluptatem.</p>
    <span class="btn">READ MORE</span>
  </div>
</section>

<div class="abs contact-band"></div>
<h2 class="abs contact-title center">CONTACT US</h2>
<p class="abs contact-lead lead center">Sed ut perspiciatis unde omnis iste natus error sit voluptatem accusantium doloremque laudantium, totam rem aperiam, eaque ipsa quae ab illo inventore veritatis et quasi architecto.</p>
<div class="abs field" style="top:3382px">Name:</div>
<div class="abs field" style="top:3416px">Email:</div>
<div class="abs field" style="top:3450px">Phone:</div>
<div class="abs field" style="top:3484px">Job:</div>
<div class="abs message">Message:</div>
<div class="abs btn contact-btn">CONTACT US QUICKLY</div>

<h2 class="abs partners-title center">PARTNERS</h2>
<p class="abs partners-lead lead center">Sed ut perspiciatis unde omnis iste natus error sit voluptatem accusantium doloremque laudantium, totam rem aperiam, eaque ipsa quae ab illo inventore veritatis et quasi architecto.</p>
<div class="abs badge" style="left:302px;width:112px"></div>
<div class="abs badge" style="left:448px;width:104px"></div>
<div class="abs badge" style="left:592px;width:184px"></div>
<div class="abs badge" style="left:812px;width:90px"></div>

<footer class="abs footer">
  <div class="brand"><span class="brand-dot"></span>NEXORA</div>
  <div class="fcol" style="left:488px"><h4>Information</h4>Sed ut perspiciatis<br>Unde omnis iste natus<br>Voluptatem accusan<br>Totam doloremque<br>Laudantium</div>
  <div class="fcol" style="left:710px"><h4>Links</h4>Sed ut perspiciatis<br>Unde omnis iste natus<br>Voluptatem accusan<br>Totam doloremque<br>Laudantium</div>
  <div class="fcol" style="left:911px"><h4>Contact</h4>
    <div class="row"><svg width="8" height="11" viewBox="0 0 10 14"><path d="M5 0a5 5 0 0 1 5 5c0 4-5 9-5 9S0 9 0 5a5 5 0 0 1 5-5z" fill="#1fa6a6"/></svg>Lindenhof 14,</div>
    <div class="row" style="padding-left:16px">3512 KP Veldhoven</div>
    <div class="row"><svg width="10" height="10" viewBox="0 0 10 10"><path d="M1 1h3l1 2-1.5 1.5a6 6 0 0 0 2.5 2.5L7.5 5.5 9.5 6.5V9C5 9 1 5 1 1z" fill="#1fa6a6"/></svg>Phone: 030-5512840</div>
    <div class="row"><svg width="10" height="8" viewBox="0 0 10 8"><rect width="10" height="8" fill="#1fa6a6"/><path d="M0 0l5 4 5-4" fill="none" stroke="#0c1217"/></svg>Email: info@nexora-it.nl</div>
  </div>
  <div class="copy">© 2018 Nexora All rights are reserved. Privacy | Terms of use</div>
  <div class="social"><i></i><i></i><i></i><i></i></div>
</footer>

</body>
</html>
```